KVR Inc Web Design

WHAT ARE WE DOING?
We are developing a new website look and feel for a new company called KVR Inc. This new look and feel should include colors, design elements, choice of photography and other imagery, fonts, and other user experience elements.

WHAT DO THEY DO?
KVR, Inc, makes tools for researchers who are studying protein-protein interactions. These molecules are the basic tools of biology, and serve as key targets for drug developers and disease researchers. The world of proteins is enormously complex, and companies like KVR provide researchers with critical tools that help them elucidate this world.

WHO ARE WE TALKING TO?
The target audience for this website are professional scientists working in university research or biopharma drug development. They are highly sophisticated consumers looking for key tools that will advance their research.

WHAT DO WE WANT THEM TO DO?
The site is an information resource for the customer exploring the tools that KVR sells and the scientific issues surrounding protein-protein interactions. They should be able to navigate easily to their content of choice, while the whole site should convey a professionalism that enhanced KVR’s credibility.

WHAT DOES THE KVR BRAND STAND FOR?
KVR stands for illumination. Proteins are challenging to study, and KVR exists to help shed light on their workings.

WHAT ARE THE KEY VALUES OF THE KVR BRAND?
Integrity. Innovation. Insight.

WHAT ARE THE EXECUTIONAL MANDITORIES?
The look and feel is completely up for grabs. Nothing is off the table.

WHAT ARE THE DELIVERABLES?
We need new designs for the following templates:
http://cms.marlowbench.com/
http://cms.marlowbench.com/products-and-services/instruments-3/bench-top-instruments/
http://cms.marlowbench.com/category/lab-study/

```html
<!DOCTYPE html>
<html lang="en">
<head>
<meta charset="utf-8">
<title>KVR Inc – Pipettes</title>
<link rel="stylesheet" href="https://fonts.googleapis.com/css2?family=Mulish:wght@400;600;700&family=Open+Sans:wght@400&display=swap">
<style>
  :root {
    --brand-orange: #fbb540;
    --brand-orange-dark: #f2a92e;
    --nav-pill: #5e4a33;
    --ink: #111111;
    --body-text: #555555;
    --link: #f7a823;
    --tab-active: #35b3d9;
    --tab-idle: #e3e3e3;
    --tab-text: #555555;
    --rule: #cfcfcf;
    --dropdown: #b8b8b8;
    --footer-text: #444444;
    --icon: #6a6a6a;
  }
  * { box-sizing: border-box; margin: 0; padding: 0; }
  html, body { width: 1200px; height: 1104px; overflow: hidden; background: #fff; }
  body { position: relative; font-family: "Mulish", sans-serif; color: var(--body-text); }

  .site-header { position: absolute; left: 0; top: 0; width: 1200px; height: 66px; background: var(--brand-orange); }
  .brand { position: absolute; left: 160px; top: 16px; font-size: 27px; letter-spacing: 7px; color: #fff; font-weight: 400; line-height: 1; }
  .main-nav a { position: absolute; top: 21px; font-size: 13.5px; font-weight: 700; color: #fff; text-decoration: none; line-height: 20px; white-space: nowrap; letter-spacing: -0.1px; }
  .main-nav a.is-current { top: 17px; height: 28px; padding: 4px 0; width: 152px; text-align: center; background: var(--nav-pill); border-radius: 14px; }
  .search { position: absolute; left: 913px; top: 20px; width: 126px; height: 22px; background: var(--brand-orange-dark); color: #fff8ea; font-size: 11.5px; padding: 4px 7px; }
  .search svg { position: absolute; right: 5px; top: 5px; }

  .page-title { position: absolute; left: 160px; top: 110px; font-size: 24px; font-weight: 400; color: var(--ink); }
  .section-select { position: absolute; left: 861px; top: 111px; width: 178px; height: 23px; background: var(--dropdown); color: #f5f5f5; font-size: 11.5px; padding: 5px 14px; }
  .section-select svg { position: absolute; right: 10px; top: 9px; }
  .title-rule { position: absolute; left: 160px; top: 145px; width: 880px; height: 4px; border-top: 1px solid var(--rule); border-bottom: 1px solid var(--rule); }

  .lede { position: absolute; left: 160px; top: 158px; width: 880px; font-size: 19.5px; line-height: 25px; color: var(--ink); font-weight: 400; }

  .hero-photo { position: absolute; left: 159px; top: 235px; width: 242px; height: 188px; background: linear-gradient(135deg, #dfe6ee 0%, #a9bdd3 50%, #e9eef3 100%); }

  .intro { position: absolute; left: 423px; top: 232px; width: 620px; font-size: 12.3px; line-height: 17.1px; }
  .intro p + p { margin-top: 17px; }
  .intro a, .tab-panel a { color: var(--link); text-decoration: none; font-weight: 600; }

  .tabs { position: absolute; left: 423px; top: 637px; display: flex; height: 32px; }
  .tab { position: relative; font-family: "Open Sans", sans-serif; font-size: 14px; color: var(--tab-text); background: var(--tab-idle); display: flex; align-items: center; justify-content: center; border-right: 1px solid #fff; }
  .tab.is-active { background: var(--tab-active); color: #fff; }
  .tab.is-active::after { content: ""; position: absolute; left: 50%; bottom: -6px; margin-left: -6px; border: 6px solid transparent; border-bottom: 0; border-top-color: var(--tab-active); }

  .panel-photo { position: absolute; left: 424px; top: 688px; width: 233px; height: 233px; background: linear-gradient(150deg, #6d8fb8 0%, #2f5d9c 45%, #b49c7a 100%); }
  .tab-panel { position: absolute; left: 668px; top: 687px; width: 376px; font-size: 12.3px; line-height: 17.1px; }
  .tab-panel p + p { margin-top: 17px; }

  .site-footer { position: absolute; left: 160px; top: 969px; width: 880px; text-align: center; }
  .footer-rule { height: 3px; border-top: 1px solid var(--rule); border-bottom: 1px solid var(--rule); }
  .footer-accent { width: 25px; height: 3px; margin: 22px auto 0; background: var(--brand-orange); position: relative; }
  .footer-accent::after { content: ""; position: absolute; left: 10px; top: 0; width: 4px; height: 3px; background: var(--nav-pill); }
  .footer-nav { margin-top: 11px; font-size: 11.5px; color: var(--footer-text); }
  .footer-nav a { color: var(--footer-text); text-decoration: none; }
  .footer-nav span { margin: 0 5px; }
  .copyright { margin-top: 4px; font-size: 12px; color: var(--footer-text); }
  .social { display: flex; justify-content: center; gap: 4px; margin-top: 6px; }
  .social span { width: 18px; height: 18px; border-radius: 50%; background: var(--icon); }
</style>
</head>
<body>
  <header class="site-header">
    <div class="brand">KVR INC</div>
    <nav class="main-nav">
      <a href="#" style="left:331px">Company</a>
      <a href="#" class="is-current" style="left:403px">Products &amp; Services</a>
      <a href="#" style="left:566px">Learning Center</a>
      <a href="#" style="left:692px">Events</a>
      <a href="#" style="left:757px">KVR News</a>
      <a href="#" style="left:840px">Contact</a>
    </nav>
    <div class="search">Search
      <svg width="12" height="12" viewBox="0 0 12 12" fill="none" stroke="#e8d5b0" stroke-width="1.6"><circle cx="5" cy="5" r="3.6"/><line x1="7.6" y1="7.6" x2="11" y2="11"/></svg>
    </div>
  </header>

  <h1 class="page-title">PIPETTES</h1>
  <div class="section-select">Product Overview
    <svg width="11" height="6" viewBox="0 0 11 6"><path d="M0 0h11L5.5 6z" fill="#eeeeee"/></svg>
  </div>
  <div class="title-rule"></div>

  <p class="lede">Donec non massa lacinia, commodo eros eget, rutrum arcu. Integer tincidunt, velit id eleifend congue, odio massa consequat mauris, massa consequat</p>

  <div class="hero-photo" role="img" aria-label="Two scientists in lab coats and safety glasses working with a pipette and plant sample"></div>

  <div class="intro">
    <p>Donec auctor mollis ligula eget molestie. Aliquam erat volutpat. Curabitur sapien libero, condimentum ac nisi nec, ultricies tincidunt ipsum. Donec in iaculis metus. Mauris eleifend nisi non sapien commodo, hendrerit ornare lacus consectetur. Pellentesque faucibus, purus non dictum lacinia, ante augue pretium neque, vitae egestas dui nisi et enim. Suspendisse iaculis nibh vel lacinia rhoncus Donec auctor mollis ligula eget molestie. Aliquam erat volutpat. Curabitur sapien libero, condimentum ac nisi nec, ultricies tincidunt ipsum. Donec in iaculis metus. Mauris eleifend nisi non sapien commodo, hendrerit ornare lacus consectetur. Pellentesque faucibus, purus non dictum lacinia, ante augue pretium neque, vitae egestas dui nisi et enim.</p>
    <p>Donec auctor mollis ligula eget molestie. Aliquam erat volutpat. Curabitur sapien libero, condimentum ac nisi nec, ultricies tincidunt ipsum. Donec in iaculis metus. Mauris eleifend nisi non sapien commodo, hendrerit ornare lacus consectetur. Pellentesque faucibus, purus non dictum lacinia, ante augue pretium neque, vitae egestas dui nisi et enim. Suspendisse iaculis nibh vel lacinia rhoncus Donec auctor mollis ligula eget molestie. Aliquam erat volutpat. Curabitur sapien libero, condimentum ac nisi nec, ultricies tincidunt ipsum. Donec in iaculis metus. Mauris eleifend nisi non sapien commodo, hendrerit ornare lacus consectetur. Pellentesque faucibus, purus non dictum lacinia, ante augue pretium neque, vitae egestas dui nisi et enim.&nbsp; Donec auctor mollis ligula eget molestie. Aliquam erat volutpat. Curabitur sapien libero, <a href="#">condimentum</a> ac nisi nec, ultricies tincidunt ipsum. Donec in iaculis metus. Mauris eleifend nisi non sapien commodo, hendrerit ornare lacus consectetur. Pellentesque faucibus, purus non dictum lacinia, ante augue pretium neque, vitae egestas dui nisi et enim. Suspendisse iaculis nibh vel lacinia rhoncus Donec auctor mollis ligula eget molestie. Aliquam erat volutpat. Curabitur sapien libero, condimentum ac nisi nec, ultricies tincidunt ipsum. Donec in iaculis metus. Mauris eleifend nisi non sapien commodo, hendrerit ornare lacus consectetur. Pellentesque faucibus, purus non dictum lacinia, ante augue pretium neque, vitae egestas dui nisi et enim.</p>
  </div>

  <nav class="tabs">
    <div class="tab is-active" style="width:128px">Overview</div>
    <div class="tab" style="width:117px">Features</div>
    <div class="tab" style="width:152px">Specifications</div>
    <div class="tab" style="width:102px">FAQ's</div>
    <div class="tab" style="width:118px;border-right:0">Manuals</div>
  </nav>

  <div class="panel-photo" role="img" aria-label="Gloved researcher filling a test tube with a pipette"></div>
  <div class="tab-panel">
    <p>Quisque feugiat lacus vitae posuere blandit. Nulla sit amet laoreet felis, id rhoncus nisl. Aenean fringilla quam in nibh egestas, in malesuada tortor accumsan. Donec non massa lacinia, commodo eros eget, rutrum arcu. Integer tincidunt, velit id eleifend congue, odio massa consequat mauris, a scelerisque nulla nulla eu nulla. Cras luctus pulvinar nibh ut viverra. Aenean vestibulum vitae justo non dictum. Mauris ut tellus in dui pretium dictum nec non tortor. Nulla a velit quis dolor interdum <a href="#">scelerisque</a> eu et nisl.</p>
    <p>Donec auctor mollis ligula eget molestie. Aliquam erat volutpat. Curabitur sapien libero, condimentum ac nisi nec, ultricies tincidunt ipsum. Donec in iaculis metus. Mauris eleifend nisi non sapien commodo, hendrerit ornare lacus consectetur. Pellentesque faucibus, purus non dictum lacinia, ante augue</p>
  </div>

  <footer class="site-footer">
    <div class="footer-rule"></div>
    <div class="footer-accent"></div>
    <div class="footer-nav">
      <a href="#">Company</a><span>-</span><a href="#">Products &amp; Services</a><span>-</span><a href="#">Learning Center</a><span>-</span><a href="#">Events</a><span>-</span><a href="#">KVR News</a><span>-</span><a href="#">Contact</a>
    </div>
    <div class="copyright">Copyright © KVR Inc. 2013</div>
    <div class="social" aria-label="Social links"><span></span><span></span><span></span></div>
  </footer>
</body>
</html>
```